Business Card Design Project

This is the first time we use our new logo. We need a business card that we can use both on our institutional corporate relationships and also that works for our staff that deals with consumers directly.

VELUNDA is a new company dedicated to empower consumers and to provide them with the best choices for specialized health care using the latest telemedicine technology (medicine at a distance via videoconference).

We want to print this cards in high quality materials and process. We will like designs that allow us to use UV spot varnish and other techniques that will differentiate us.

We are including Two different versions of Color logos. In addition we are including white over black background logos. Those can be used replacing the black for a color.

Please note this is the first time we will be creating any corporate materials with our new logo and colors.

Target Market(s)

34+ consumers of medium high and high socioeconomic levels.

Industry/Entity Type

Health

Requirements
Must have
• Our logo on its original colors
Should not have
• Any other graphical element or design that is not our logo

```html
<!DOCTYPE html>
<html lang="en">
<head>
<meta charset="utf-8">
<title>VELUNDA Business Card</title>
<link rel="stylesheet" href="https://fonts.googleapis.com/css2?family=Montserrat:wght@500;700&family=Arimo:wght@400&display=swap">
<style>
  :root {
    --navy: #1b5680;
    --teal: #1ba3a0;
    --sky: #4fb3dc;
    --paper: #ffffff;
    --backdrop: #e9ecef;
    --ink: #222222;
  }
  * { margin: 0; padding: 0; box-sizing: border-box; }
  html, body {
    width: 1200px;
    height: 1057px;
    overflow: hidden;
    background: var(--backdrop);
  }
  .canvas {
    position: relative;
    width: 1200px;
    height: 1057px;
  }
  .card {
    position: absolute;
    left: 250px;
    width: 700px;
    height: 400px;
    overflow: hidden;
    box-shadow: 0 6px 18px rgba(0,0,0,0.18);
  }
  .card-front { top: 90px; background: var(--paper); }
  .card-back { top: 567px; background: var(--navy); }

  .front-band {
    position: absolute;
    left: 0; top: 0;
    width: 140px; height: 100%;
    background: var(--navy);
  }
  .front-rule {
    position: absolute;
    left: 152px; top: 0;
    width: 3px; height: 100%;
    background: var(--sky);
  }
  .brand-dot {
    position: absolute;
    left: 112px; top: 58px;
    width: 76px; height: 76px;
    border-radius: 50%;
    background: var(--sky);
    border: 6px solid var(--paper);
  }
  .brand-name {
    position: absolute;
    left: 205px; top: 62px;
    font-family: "Montserrat", sans-serif;
    font-weight: 700;
    font-size: 58px;
    letter-spacing: 3px;
    color: var(--navy);
    line-height: 1;
  }
  .contact-list {
    position: absolute;
    left: 185px; top: 196px;
    list-style: none;
    font-family: "Arimo", sans-serif;
    font-size: 17px;
    color: var(--ink);
  }
  .contact-list li {
    display: flex;
    align-items: center;
    height: 27px;
  }
  .contact-list svg {
    width: 15px; height: 15px;
    margin-right: 9px;
    flex: none;
  }
  .contact-address {
    margin-top: 14px;
    padding-left: 24px;
  }
  .person {
    position: absolute;
    right: 50px; top: 186px;
    text-align: right;
  }
  .person-name {
    font-family: "Montserrat", sans-serif;
    font-weight: 700;
    font-size: 27px;
    color: var(--navy);
  }
  .person-title {
    font-family: "Montserrat", sans-serif;
    font-weight: 500;
    font-size: 19px;
    color: var(--teal);
  }

  .back-mark {
    position: absolute;
    left: 0; top: 108px;
    width: 100%;
    display: flex;
    justify-content: center;
    align-items: center;
    gap: 18px;
  }
  .back-dot {
    width: 50px; height: 50px;
    border-radius: 50%;
    border: 8px solid var(--paper);
  }
  .back-name {
    font-family: "Montserrat", sans-serif;
    font-weight: 700;
    font-size: 60px;
    letter-spacing: 4px;
    color: var(--paper);
    line-height: 1;
  }
  .back-web {
    position: absolute;
    left: 0; top: 300px;
    width: 100%;
    text-align: center;
    font-family: "Arimo", sans-serif;
    font-size: 24px;
    letter-spacing: 7px;
    color: var(--paper);
  }
</style>
</head>
<body>
<main class="canvas">
  <section class="card card-front" aria-label="Card front">
    <div class="front-band"></div>
    <div class="front-rule"></div>
    <div class="brand-dot"></div>
    <div class="brand-name">VELUNDA</div>

    <ul class="contact-list">
      <li>
        <svg viewBox="0 0 16 16" aria-hidden="true"><circle cx="8" cy="8" r="7" fill="none" stroke="#1b5680" stroke-width="1.5"/><path d="M5.5 4.5l1.5 0 .7 2-1 .8a5 5 0 0 0 2 2l.8-1 2 .7v1.5c-3.5.5-6.5-2.5-6-6z" fill="#1b5680"/></svg>
        012-345-6789
      </li>
      <li>
        <svg viewBox="0 0 16 16" aria-hidden="true"><circle cx="8" cy="8" r="7" fill="none" stroke="#1b5680" stroke-width="1.5"/><path d="M5.5 4.5l1.5 0 .7 2-1 .8a5 5 0 0 0 2 2l.8-1 2 .7v1.5c-3.5.5-6.5-2.5-6-6z" fill="#1b5680"/></svg>
        012-345-6789
      </li>
      <li>
        <svg viewBox="0 0 16 16" aria-hidden="true"><rect x="1" y="3.5" width="14" height="9" rx="1" fill="#1b5680"/><path d="M1.5 4l6.5 5 6.5-5" fill="none" stroke="#ffffff" stroke-width="1.2"/></svg>
        name@velunda.com
      </li>
      <li>
        <svg viewBox="0 0 16 16" aria-hidden="true"><circle cx="8" cy="8" r="7" fill="none" stroke="#1b5680" stroke-width="1.5"/><ellipse cx="8" cy="8" rx="3" ry="7" fill="none" stroke="#1b5680" stroke-width="1.2"/><path d="M1 8h14M2.5 4.5h11M2.5 11.5h11" stroke="#1b5680" stroke-width="1"/></svg>
        www.velunda.com
      </li>
      <li class="contact-address">Street Name, City Name, State, City Zip Code</li>
    </ul>

    <div class="person">
      <div class="person-name">Your Name</div>
      <div class="person-title">Title</div>
    </div>
  </section>

  <section class="card card-back" aria-label="Card back">
    <div class="back-mark">
      <div class="back-dot"></div>
      <div class="back-name">VELUNDA</div>
    </div>
    <div class="back-web">www.velunda.com</div>
  </section>
</main>
</body>
</html>
```